This book will apply the 12 Steps to gaming addiction, also known as video game addiction. The primary purpose of the book is to provide an effective solution for this new type of addiction. The solution is based on the rich and successful concepts of traditional twelve-step programs like RQ.

The title on the cover will be "Nine Doors Out of the Endless Level" and "by Peter Halvorn". A subtitle can be used if it works in your design of "A Practical Path Back from Compulsive Screen Play". Cover will be for a 6" x 9" book approximately 110 pages in length.

Some back cover text including some review quotes and an author bio are in the attached Word doc. There is also an author photo attached for for the back cover.

Requirements
Must have
• For the cover design it could be stylized, or an image, a partial image, or whatever. I am open to suggestions. Think about what would be noticed by a person searching for help with moderating their video game use, or by the parents or loved ones of problem gamers. Something contemporary and eye catching.

```html
<!DOCTYPE html>
<html lang="en">
<head>
<meta charset="utf-8">
<title>Nine Doors Out of the Endless Level — Book Cover</title>
<link href="https://fonts.googleapis.com/css2?family=Saira+Condensed:wght@500;600;700&family=Saira:wght@500&family=Poppins:wght@400;600;700&display=swap" rel="stylesheet">
<style>
  :root {
    --page-bg: #e9e7e4;
    --cover-ink: #07080f;
    --cover-navy: #0b1230;
    --glow-blue: #2c56c9;
    --glow-cyan: #4fb6e8;
    --glow-red: #b8323c;
    --orange-light: #f9b083;
    --orange-deep: #ee7f63;
    --lavender-light: #d4d2f4;
    --lavender-deep: #8497db;
    --rule-blue: #7e93cf;
    --text-white: #f4f5fa;
    --reviewer: #b9bce6;
  }
  * { margin: 0; padding: 0; box-sizing: border-box; }
  html, body {
    width: 1200px; height: 1000px; overflow: hidden;
    background: var(--page-bg);
  }
  .canvas {
    position: relative; width: 1200px; height: 1000px;
  }
  .book-cover {
    position: absolute; left: 290px; top: 35px;
    width: 620px; height: 930px; overflow: hidden;
    background: linear-gradient(180deg, var(--cover-ink) 0%, #0a0d22 40%, var(--cover-navy) 100%);
    box-shadow: 0 12px 30px rgba(0,0,0,.25);
  }
  .controller-photo {
    position: absolute; left: 0; top: 420px; width: 620px; height: 510px;
    background:
      radial-gradient(ellipse 160px 120px at 120px 210px, rgba(184,50,60,.55), transparent 70%),
      radial-gradient(ellipse 140px 110px at 520px 480px, rgba(200,60,70,.5), transparent 70%),
      radial-gradient(ellipse 220px 160px at 330px 230px, rgba(79,182,232,.55), transparent 70%),
      radial-gradient(ellipse 300px 220px at 250px 300px, rgba(44,86,201,.7), transparent 75%),
      radial-gradient(ellipse 200px 120px at 80px 470px, rgba(120,160,230,.35), transparent 70%),
      linear-gradient(180deg, var(--cover-ink) 0%, #0e1a4a 45%, #142266 100%);
  }
  .cover-veil {
    position: absolute; left: 0; top: 400px; width: 620px; height: 200px;
    background: linear-gradient(180deg, var(--cover-ink) 10%, rgba(7,8,15,.6) 60%, transparent 100%);
  }
  .title-art { position: absolute; left: 0; top: 0; width: 620px; height: 430px; }
  .title-art text { font-family: "Saira Condensed", "Arial Narrow", sans-serif; font-weight: 600; }
  .review {
    position: absolute; left: 40px; top: 455px; width: 540px;
    text-align: center; color: var(--text-white);
  }
  .review-quote {
    font-family: "Poppins", Arial, sans-serif; font-weight: 700;
    font-size: 15.5px; line-height: 1.5;
  }
  .review-name {
    margin-top: 22px;
    font-family: "Poppins", Arial, sans-serif; font-weight: 700;
    font-size: 14px; letter-spacing: .02em; color: var(--reviewer);
  }
  .review-role {
    font-family: "Poppins", Arial, sans-serif; font-weight: 400;
    font-size: 14px;
  }
  .author-name {
    position: absolute; left: 0; bottom: 40px; width: 620px;
    text-align: center;
    font-family: "Saira", Arial, sans-serif; font-weight: 500;
    font-size: 54px; letter-spacing: .22em; padding-left: .22em;
    color: var(--text-white);
  }
</style>
</head>
<body>
<div class="canvas">
  <section class="book-cover">
    <div class="controller-photo" role="img" aria-label="Close-up photograph of a translucent game controller with blue and red bokeh lights"></div>
    <div class="cover-veil"></div>

    <svg class="title-art" viewBox="0 0 620 430" aria-label="Nine Doors Out of the Endless Level">
      <defs>
        <linearGradient id="orangeFill" x1="0" y1="0" x2="1" y2="1">
          <stop offset="0" stop-color="var(--orange-light)"/>
          <stop offset="1" stop-color="var(--orange-deep)"/>
        </linearGradient>
        <linearGradient id="lavenderFill" x1="0" y1="0" x2="1" y2="0">
          <stop offset="0" stop-color="var(--lavender-light)"/>
          <stop offset="1" stop-color="var(--lavender-deep)"/>
        </linearGradient>
      </defs>
      <g class="title-bracket" stroke="var(--rule-blue)" stroke-width="2" fill="none">
        <path d="M65 80 H232 V406"/>
        <path d="M232 125 H262"/>
      </g>
      <circle cx="268" cy="125" r="7" fill="var(--rule-blue)"/>
      <circle cx="238" cy="408" r="7" fill="var(--rule-blue)"/>

      <text x="65" y="310" font-size="230" fill="url(#orangeFill)" textLength="150" lengthAdjust="spacingAndGlyphs">NINE</text>
      <text x="66" y="410" font-size="78" fill="url(#orangeFill)" textLength="148" lengthAdjust="spacingAndGlyphs">DOORS</text>

      <text x="285" y="150" font-size="46" fill="var(--text-white)" textLength="295" lengthAdjust="spacingAndGlyphs">OUT OF THE</text>
      <text x="258" y="275" font-size="128" fill="url(#lavenderFill)" textLength="322" lengthAdjust="spacingAndGlyphs">ENDLESS</text>
      <text x="258" y="410" font-size="142" fill="url(#orangeFill)" textLength="322" lengthAdjust="spacingAndGlyphs">LEVEL</text>
    </svg>

    <div class="review">
      <p class="review-quote">“A must-read for anyone who is addicted to or thinks they may have a problem with digital gaming...”</p>
      <p class="review-name">DALE MARROW</p>
      <p class="review-role">Noted Interventionist and Keynote Speaker</p>
    </div>

    <p class="author-name">PETER HALVORN</p>
  </section>
</div>
</body>
</html>
```